New Alcoholic Spiked Seltzer Line

We need a can design for a line of low calorie alcoholic seltzer. This product is a sparkling water and vodka drink with no sugar added in a slim 12 oz can.

This is a lighter, healthier, alternative to the sugary ready-to-drinks on the market. The product contains only 3 ingredients: Vodka, Water and Natural Flavors. It has only 100 calories but still has 5% alcohol, so you don't need to sacrifice alcohol to cut calories.

This product also does not contain any preservatives.

We want this design to communicate the following objectives to the consumer and in this order:

1. Appetizing product
2.Low calorie
3.Communicate the type of beverage (Spiked Seltzer)

The brand name of the product is VELKA.

The flavor of the product needed to be used for the design is Mango-Orange.

Comparable products are:

www.brindlefizzworks.example/
https://www.quorvabubbles.example
https://pelnavo.example/

The designs should not infringe or copy the creative directions of the products mentionned above. They are only given so that you can better understand the type of product we are developing.

Target Market(s)

Young Professional women between the ages of 25 and 44

Industry/Entity Type

Product

Colors

Designer to choose colors to be used in the design.

Requirements
Must have
• Design extendibility, meaning it can be adapted for other flavors.
• This is a new category in the market we are targeting, so consumers must easily be able to identify what type of product this is.

```html
<!DOCTYPE html>
<html lang="en">
<head>
<meta charset="utf-8">
<title>VELKA Spiked Seltzer – Mango-Orange can label</title>
<link rel="stylesheet" href="https://fonts.googleapis.com/css2?family=Montserrat:wght@400;600;700;800&display=swap">
<style>
  :root {
    --label-white: #ffffff;
    --ink: #1a1a1a;
    --flavor-pink: #e8457f;
    --wash-pink: #ec3f8e;
    --wash-magenta: #d93a9c;
    --wash-orange: #f4a35a;
    --wash-peach: #f8c48c;
  }
  * { margin: 0; padding: 0; box-sizing: border-box; }
  html, body {
    width: 1200px;
    height: 2800px;
    overflow: hidden;
    background: var(--label-white);
  }
  .can-label {
    position: relative;
    width: 1200px;
    height: 2800px;
    background: var(--label-white);
    font-family: "Montserrat", Arial, sans-serif;
    color: var(--ink);
    overflow: hidden;
  }
  .watercolor-band {
    position: absolute;
    left: 0;
    width: 1200px;
  }
  .watercolor-band--top { top: 340px; height: 860px; }
  .watercolor-band--bottom { top: 1740px; height: 760px; }

  .brand-lockup {
    position: absolute;
    top: 760px;
    left: 0;
    width: 1200px;
    text-align: center;
  }
  .brand-name {
    display: inline-flex;
    align-items: center;
    gap: 40px;
    font-size: 170px;
    font-weight: 600;
    letter-spacing: 24px;
    line-height: 1;
    color: var(--ink);
  }
  .brand-mark {
    width: 80px;
    height: 80px;
    border-radius: 50%;
    background: var(--ink);
  }
  .product-type {
    margin-top: 110px;
    font-size: 104px;
    font-weight: 800;
    letter-spacing: 4px;
    line-height: 1;
    color: var(--ink);
  }

  .flavor-block {
    position: absolute;
    top: 1330px;
    left: 0;
    width: 1200px;
    text-align: center;
  }
  .flavor-intro {
    font-size: 54px;
    font-weight: 600;
    line-height: 1.2;
  }
  .flavor-name {
    margin-top: 12px;
    font-size: 84px;
    font-weight: 400;
    color: var(--flavor-pink);
    line-height: 1.1;
  }
  .calorie-callout {
    margin-top: 14px;
    font-size: 44px;
    font-weight: 800;
    letter-spacing: 1px;
    line-height: 1.2;
  }

  .abv {
    position: absolute;
    top: 2580px;
    left: 0;
    width: 1200px;
    text-align: center;
    font-size: 44px;
    font-weight: 600;
  }
</style>
</head>
<body>
<main class="can-label">

  <svg class="watercolor-band watercolor-band--top" viewBox="0 0 1200 860" role="img"
       aria-label="Diagonal pink and orange watercolor brush strokes">
    <defs>
      <linearGradient id="top-wash" x1="0" y1="0" x2="1" y2="1">
        <stop offset="0" stop-color="var(--wash-magenta)"/>
        <stop offset="0.45" stop-color="var(--wash-pink)"/>
        <stop offset="0.7" stop-color="var(--wash-orange)"/>
        <stop offset="1" stop-color="var(--wash-peach)"/>
      </linearGradient>
    </defs>
    <path d="M0 40 C 300 0, 800 120, 1200 200 L 1200 720 C 900 640, 400 420, 0 300 Z"
          fill="url(#top-wash)" opacity="0.85"/>
  </svg>

  <svg class="watercolor-band watercolor-band--bottom" viewBox="0 0 1200 760" role="img"
       aria-label="Diagonal orange and pink watercolor brush strokes">
    <defs>
      <linearGradient id="bottom-wash" x1="0" y1="1" x2="1" y2="0">
        <stop offset="0" stop-color="var(--wash-peach)"/>
        <stop offset="0.35" stop-color="var(--wash-orange)"/>
        <stop offset="0.65" stop-color="var(--wash-pink)"/>
        <stop offset="1" stop-color="var(--wash-magenta)"/>
      </linearGradient>
    </defs>
    <path d="M0 520 C 350 380, 800 160, 1200 20 L 1200 320 C 800 460, 380 640, 0 760 Z"
          fill="url(#bottom-wash)" opacity="0.85"/>
  </svg>

  <header class="brand-lockup">
    <div class="brand-name"><span class="brand-mark" aria-hidden="true"></span>VELKA</div>
    <div class="product-type">SPIKED SELTZER</div>
  </header>

  <section class="flavor-block">
    <p class="flavor-intro">Natural Flavors of</p>
    <p class="flavor-name">Mango-Orange</p>
    <p class="calorie-callout">ONLY 100 CALORIES!</p>
  </section>

  <p class="abv">5% alc./vol.</p>

</main>
</body>
</html>
```